Property Portal needs Chatterloop Cover Image and Sponsor Ad Design

WHO WE ARE
Hi Pitchers! We are an advertising portal that focus on presenting the latest property launches in Singapore. Our platform and interface will provide consumer an enjoyable and easy browsing experience looking for their ideal property to buy/invest, while ensuring updated information, images/videos, and other useful description is provided on each project.

WHAT WE NEED
Our website is www.brightkeyhomes.sg, and we need designs for our Chatterloop page www.facebook.com/brightkeyhomes. One as the Cover Image (815 x 315), and one as our Sponsor Ad Image (1200 x 627). The 2 designs can be similar or different.

DESIGN
We want to convey a professional and sociable feel. A "cool" and elegant design may be suitable, although feel free to have your own look & feel as long as it suits our purpose. Try to have a focus, and not look messy. We don't want to look cheap, spammy or boring in any sense. Be creative and purposeful =) You may use the snapvault images attached or you can use your own. Add symbols or graphics if it helps to give the design a better feel.

For your reference, I find there is a number of good designs with nice look & feel in this project including those withdraw/eliminated.
http://chatterloop.pitchmart.example/contest.aspx?id=218907&page=2
http://chatterloop.pitchmart.example/contest.aspx?id=218907

IDEAS
You may want to embed our portal in an SLATEX device as part of the design (see samples below but replace callpod with SlateX). And/or you can have a blur-out image background to have a focus on what you want to show. Please note that we are not restricting any other designs concept, this is just an idea I have.

CAPTIONS
You may use one or a few of the sample captions below.
- Singapore Latest Property Launches In One Portal (slight emphasis on "in one portal")
- Latest Projects • Updated Info • Best Pricing
- Residential • Commercial • Overseas (perhaps label on images)

Hope we can find an ideal design here. We will request from pitchmart to increase the project budget to give out more participation payments if there is a few good ones. We are also looking to find suitable designers for our future projects as we need a few more designs. If you have questions, feel free to ask me and I will reply promptly.

Reason: Project cancelled and relaunch with different purpose, moved from Newsletter to Chatterloop Design.

IDEAS (UPDATED) I am thinking one way to showcase our portal is perhaps to have our website embedded in an slatex and/or notebook pro device as part of the design. I've attached some designs I came across to show what I mean (only the embedding part). If you are going to do it this way, you can use our main page www.brightkeyhomes.sg and/or a project page www.brightkeyhomes.sg/willowcrest-at-ambergate to display

Target Market(s)

Real Estate Agents, Investors, Developers, General public age 30 & above

Industry/Entity Type

Advertising

Colors
9ccb3b
00a98f
0592cd
3176b5
ffcf3e
5c5c5c

Requirements
Should not have
• I prefer not to use real people stock images unless you are very sure it will work out well.

```html
<!DOCTYPE html>
<html lang="en">
<head>
<meta charset="utf-8">
<title>Brightkeyhomes – Chatterloop Cover and Sponsor Ad</title>
<link rel="stylesheet" href="https://fonts.googleapis.com/css2?family=Squada+One&family=PT+Sans:wght@400;700&display=swap">
<style>
  :root {
    --board: #1d1d1d;
    --label: #f2f2f2;
    --paper: #f4f4f4;
    --paper-edge: #e2e2e2;
    --green-dark: #3bb54a;
    --green-light: #8cc63f;
    --green-ribbon: #2e9a3e;
    --ink: #5c5c5c;
    --ink-dark: #333333;
    --skyline: #d4d4d4;
  }
  * { margin: 0; padding: 0; box-sizing: border-box; }
  html, body { width: 1200px; height: 1072px; overflow: hidden; }
  body {
    background: var(--board);
    font-family: "PT Sans", sans-serif;
    position: relative;
  }
  .section-label {
    position: absolute;
    left: 0; width: 1200px;
    text-align: center;
    color: var(--label);
    font-size: 23px;
    letter-spacing: 0.5px;
  }
  .section-label.cover-label { top: 47px; }
  .section-label.ad-label { top: 479px; }

  /* ---------- Cover ---------- */
  .cover {
    position: absolute;
    left: 175px; top: 86px;
    width: 851px; height: 315px;
    background: linear-gradient(180deg, #f7f7f7 0%, var(--paper) 60%, #ececec 100%);
    overflow: hidden;
  }
  .cover .ribbon {
    position: absolute; left: 18px; top: 0;
    width: 70px; height: 90px;
  }
  .cover .ribbon-text {
    position: absolute; left: 18px; top: 24px; width: 70px;
    text-align: center;
    font-family: "Squada One", sans-serif;
    color: #fff; font-size: 17px; line-height: 23px;
  }
  .cover .brand-name {
    position: absolute; left: 0; top: 42px; width: 851px;
    text-align: center;
    font-family: "Squada One", sans-serif;
    font-size: 24px; color: var(--ink-dark);
  }
  .cover .headline-top {
    position: absolute; left: 0; top: 96px; width: 851px;
    text-align: center;
    font-family: "Squada One", sans-serif;
    font-size: 36px; color: var(--green-light);
  }
  .cover .headline-main {
    position: absolute; left: 0; top: 130px; width: 851px;
    text-align: center;
    font-family: "Squada One", sans-serif;
    font-size: 60px; color: var(--green-dark);
  }
  .cover .tagline {
    position: absolute; left: 0; top: 193px; width: 851px;
    text-align: center;
    font-size: 13px; color: var(--ink-dark);
  }
  .tagline .dot { color: var(--green-dark); margin: 0 5px; }
  .skyline {
    position: absolute;
    background: linear-gradient(180deg, rgba(200,200,200,0.9) 0%, rgba(225,225,225,0.5) 70%, rgba(240,240,240,0) 100%);
  }
  .cover .skyline { left: 40px; top: 222px; width: 770px; height: 93px; }

  /* ---------- Sponsor ad ---------- */
  .sponsor {
    position: absolute;
    left: 127px; top: 520px;
    width: 947px; height: 495px;
    background: linear-gradient(135deg, #ffffff 0%, var(--paper) 55%, #e9e9e9 100%);
    overflow: hidden;
  }
  .sponsor .streaks { position: absolute; left: 0; top: 0; }
  .sponsor .brand-name {
    position: absolute; left: 24px; top: 64px;
    font-size: 44px; font-weight: 400; color: var(--green-dark);
    letter-spacing: -0.5px;
  }
  .sponsor .headline-top {
    position: absolute; left: 24px; top: 214px;
    font-size: 24px; color: var(--ink);
  }
  .sponsor .headline-main {
    position: absolute; left: 24px; top: 244px;
    font-size: 31px; font-weight: 700; color: var(--green-dark);
  }
  .sponsor .skyline { left: 250px; top: 415px; width: 650px; height: 80px; }
  .contact-list {
    position: absolute; left: 24px; top: 397px;
    list-style: none;
  }
  .contact-list li {
    display: flex; align-items: center;
    height: 30px;
    font-size: 14px; color: var(--ink-dark);
  }
  .contact-list svg { width: 24px; height: 24px; margin-right: 6px; }
  .sponsor .gallery { position: absolute; left: 0; top: 0; }
</style>
</head>
<body>

<div class="section-label cover-label">Chatterloop&nbsp; Cover</div>

<section class="cover">
  <svg class="ribbon" viewBox="0 0 70 90" aria-hidden="true">
    <polygon points="0,0 70,0 70,72 35,90 0,72" fill="var(--green-ribbon)"/>
    <polygon points="0,72 35,90 70,72 70,76 35,94 0,76" fill="#1f6f2b"/>
  </svg>
  <div class="ribbon-text">OFFICIAL<br>PAGE</div>
  <div class="brand-name">brightkeyhomes.sg</div>
  <div class="headline-top">Singapore Latest Property</div>
  <div class="headline-main">Launches In One Portal</div>
  <div class="tagline">Latest Projects<span class="dot">•</span>Updated Info<span class="dot">•</span>Best Pricing</div>
  <div class="skyline" role="img" aria-label="Faint grey Singapore city skyline silhouette"></div>
</section>

<div class="section-label ad-label">Sponsor Ad</div>

<section class="sponsor">
  <svg class="streaks" width="947" height="495" aria-hidden="true">
    <polygon points="600,0 640,0 420,260 380,260" fill="#ffffff" opacity="0.7"/>
    <polygon points="760,0 800,0 560,300 520,300" fill="#e6e6e6" opacity="0.6"/>
    <polygon points="20,0 60,0 0,70 0,25" fill="#e4e4e4" opacity="0.7"/>
  </svg>

  <div class="brand-name">brightkeyhomes.sg</div>
  <div class="headline-top">Singapore Latest Property</div>
  <div class="headline-main">Launches In One Portal</div>

  <div class="skyline" role="img" aria-label="Faint grey Singapore city skyline silhouette"></div>

  <svg class="gallery" width="947" height="495">
    <defs>
      <linearGradient id="photo-condo" x1="0" y1="0" x2="0" y2="1">
        <stop offset="0" stop-color="#8fb8d8"/>
        <stop offset="0.5" stop-color="#c9b9a2"/>
        <stop offset="1" stop-color="#6f8f4e"/>
      </linearGradient>
      <linearGradient id="photo-pool" x1="0" y1="0" x2="0" y2="1">
        <stop offset="0" stop-color="#a9c9e4"/>
        <stop offset="0.6" stop-color="#e8e8e8"/>
        <stop offset="1" stop-color="#3f9ccf"/>
      </linearGradient>
      <linearGradient id="photo-tower" x1="0" y1="0" x2="0" y2="1">
        <stop offset="0" stop-color="#d9b98a"/>
        <stop offset="0.6" stop-color="#8c7a63"/>
        <stop offset="1" stop-color="#3c5a5a"/>
      </linearGradient>
      <linearGradient id="photo-night" x1="0" y1="0" x2="0" y2="1">
        <stop offset="0" stop-color="#4a3a5a"/>
        <stop offset="1" stop-color="#b07a4a"/>
      </linearGradient>
    </defs>

    <circle cx="766" cy="252" r="175" fill="var(--green-dark)"/>
    <circle cx="766" cy="252" r="150" fill="url(#photo-condo)" role="img" aria-label="Low-rise residential development with trees"/>

    <circle cx="443" cy="285" r="78" fill="var(--green-dark)"/>
    <circle cx="443" cy="285" r="60" fill="url(#photo-pool)" role="img" aria-label="White condominium towers beside a pool"/>

    <circle cx="548" cy="140" r="107" fill="var(--green-light)"/>
    <circle cx="548" cy="140" r="88" fill="url(#photo-condo)" role="img" aria-label="Modern apartment block with palm trees"/>

    <circle cx="573" cy="262" r="97" fill="var(--green-light)"/>
    <circle cx="573" cy="262" r="80" fill="url(#photo-tower)" role="img" aria-label="Twin residential high-rise towers at dusk"/>

    <circle cx="660" cy="170" r="66" fill="var(--green-light)"/>
    <circle cx="660" cy="170" r="52" fill="url(#photo-pool)" role="img" aria-label="Residential towers across a waterfront"/>

    <circle cx="458" cy="198" r="36" fill="var(--green-light)"/>
    <circle cx="458" cy="198" r="26" fill="url(#photo-night)" role="img" aria-label="Lit condominium at night"/>
  </svg>

  <ul class="contact-list">
    <li>
      <svg viewBox="0 0 24 24" aria-hidden="true"><circle cx="12" cy="12" r="10.5" fill="none" stroke="var(--ink-dark)" stroke-width="1.6"/><path d="M8.5 6.5c-.8.4-1.5 1.3-1.2 2.6.7 3.3 3.4 6.3 6.6 7.5 1.3.4 2.3-.3 2.7-1.1l-2-1.6-1.3.9c-1.5-.7-2.7-2-3.3-3.5l1-1.2z" fill="var(--ink-dark)"/></svg>
      +(65) 61234580
    </li>
    <li>
      <svg viewBox="0 0 24 24" aria-hidden="true"><circle cx="12" cy="12" r="10.5" fill="none" stroke="var(--ink-dark)" stroke-width="1.6"/><rect x="6.5" y="8" width="11" height="8" fill="none" stroke="var(--ink-dark)" stroke-width="1.5"/><path d="M6.5 8l5.5 4.5L17.5 8" fill="none" stroke="var(--ink-dark)" stroke-width="1.5"/></svg>
      admin@brightkeyhomes.sg
    </li>
    <li>
      <svg viewBox="0 0 24 24" aria-hidden="true"><circle cx="12" cy="12" r="10" fill="none" stroke="var(--ink-dark)" stroke-width="1.6"/><ellipse cx="12" cy="12" rx="4.2" ry="10" fill="none" stroke="var(--ink-dark)" stroke-width="1.4"/><path d="M2 12h20M4 7h16M4 17h16" stroke="var(--ink-dark)" stroke-width="1.4"/></svg>
      www.brightkeyhomes.sg
    </li>
  </ul>
</section>

</body>
</html>
```